Bright Trails, Strong Spirits Poster for American Indian Older Adults

We need am 11" x 17" poster designed for a health outreach project designed to reach older U.S. American Indians. The materials developed through this project will be distributed to American Indian and Alaska Native tribes, communities and tribal-serving organizations across the U.S. (more than 500 different tribes). If we find a successful design we will work with that designer to produce at least one other item we need design work for using the same look/feel and maybe other materials for this project. (more work!). The poster will include a set of facts (bulleted list on the attached document) that we would like presented in an "infographic" style. The design must be reflective of the American Indian culture and designed with older adults (65 and older) in mind. Imagery plays a strong role in the American Indian culture in the U.S. images of the heart, water, feathers, circle of life, etc. If you use photos of people they must include older adults and they must be American Indian (Native American). We prefer deep earth tones for the color scheme. The design must take into account design principles for older adults: 1. Try not to put colored font on colored background 2. Ensure high contrast for text 3. Font style should be sans serif, not cursive,decorative or heavily stylized because it is harder to read 4. Avoid using all caps 5. Don't print sideways or on top of images, shaded, backgrounds, etc. 6. All images should related specifically to the content of the text and be culturally appropriate for both older adults and American Indians. The final design should be easy to read and appeal to older American Indian adults. We need to incorporate three logos on the poster towards the bottom they should not be the center/focus of the poster. We also need to include a statement about who produced the materials- that can be very small below the logos at the bottom of the poster. We've attached the text for the poster and three logo files (note one is solid blue- we will finalize that after the document design is selected but need a placeholder for that logo.

Target Market(s)

Older adult (65 and older) American Indian and Alaska Natives and their family members in tribes, communities and tribal-serving organizations across the US

Font styles to use
Sans Serif

Requirements
Must have
• Must adhere to good design principles for older adults (listed in project description)
• Must feature culturally appropriate/targeted imagery and design look and feel

```html
<!DOCTYPE html>
<html lang="en">
<head>
<meta charset="utf-8">
<title>Bright Trails, Strong Spirits</title>
<link rel="stylesheet" href="https://fonts.googleapis.com/css2?family=Montserrat:ital,wght@0,400;0,500;0,600;0,700;0,800;1,600;1,800&display=swap">
<style>
  :root {
    --sky-top: #b8261c;
    --sky-mid: #d9481f;
    --sky-glow: #f08a2a;
    --mountain: #2f3d63;
    --water-top: #c0553a;
    --water-low: #8f2e24;
    --ink: #1c1c1c;
    --white: #ffffff;
    --card-red: #c8221e;
    --card-body: #f1f1f1;
    --clock: #d9852f;
    --footer: #ffffff;
    --partner-a: #d9532b;
    --partner-b: #2e8b3a;
  }
  * { margin: 0; padding: 0; box-sizing: border-box; }
  html, body { width: 774px; height: 1200px; overflow: hidden; background: var(--white); }
  .poster {
    position: relative;
    width: 774px;
    height: 1200px;
    overflow: hidden;
    font-family: "Montserrat", Arial, sans-serif;
    color: var(--white);
  }
  .scene {
    position: absolute; inset: 0 0 82px 0;
    background: linear-gradient(180deg,
      var(--sky-top) 0%, var(--sky-mid) 30%, var(--sky-glow) 52%,
      #c9643a 58%, var(--mountain) 64%, #4a4560 72%,
      var(--water-top) 76%, #b04a32 88%, var(--water-low) 100%);
  }
  .elder-photo {
    position: absolute; left: 542px; top: 376px; width: 232px; height: 376px;
    border-radius: 116px 116px 20px 20px;
    background: linear-gradient(180deg, #8a7b6e 0%, #6b5447 40%, #2c3c6a 75%, #25345c 100%);
  }
  .title {
    position: absolute; left: 86px; top: 28px;
    font-weight: 600; font-size: 80px; line-height: 88px; letter-spacing: -0.5px;
  }
  .title .line { display: block; white-space: nowrap; }
  .title .underlined {
    display: inline-block; padding-bottom: 6px;
    border-bottom: 5px solid var(--white);
  }
  .subtitle {
    position: absolute; left: 134px; top: 226px;
    font-weight: 500; font-size: 29px; line-height: 34px; letter-spacing: 0.5px;
  }
  .stat { position: absolute; left: 40px; display: flex; align-items: flex-start; }
  .stat-icon { width: 80px; height: 74px; margin-right: 14px; flex: none; }
  .stat-figure { font-weight: 800; font-size: 44px; line-height: 42px; color: var(--ink); letter-spacing: -1px; }
  .stat-label { font-size: 17px; line-height: 20px; color: var(--ink); font-weight: 500; margin-top: 4px; }
  .stat-us { top: 366px; }
  .stat-age { top: 460px; }
  .stat-tribe { top: 555px; }
  .map-shape { width: 80px; height: 50px; margin-top: 10px; background: #1c1c1c; border-radius: 6px 14px 10px 18px; }
  .headdress-shape { width: 68px; height: 80px; background: #1c1c1c; border-radius: 40px 30px 20px 30px; margin-left: 6px; }
  .risk-note {
    position: absolute; left: 126px; top: 700px; width: 410px;
    font-style: italic; font-weight: 600; font-size: 20px; line-height: 27px;
  }
  .risk-note strong { font-weight: 800; }
  .clock {
    position: absolute; left: 62px; top: 960px; width: 116px; height: 116px;
    border-radius: 50%; background: radial-gradient(circle, #f0b060 0%, var(--clock) 70%, #b86a2a 100%);
  }
  .appointment {
    position: absolute; left: 124px; top: 984px; width: 366px; height: 105px;
    box-shadow: 0 3px 6px rgba(0,0,0,0.35);
  }
  .appointment-head {
    height: 35px; background: var(--card-red); color: var(--white);
    font-weight: 700; font-size: 20px; line-height: 35px; text-align: center;
  }
  .appointment-body {
    height: 70px; background: linear-gradient(180deg, #ffffff, var(--card-body));
    color: var(--ink); font-size: 18.5px; line-height: 22px; font-weight: 500;
    text-align: center; padding-top: 3px;
  }
  .footer {
    position: absolute; left: 0; bottom: 0; width: 774px; height: 82px; background: var(--footer);
    display: flex; align-items: center; justify-content: flex-end; gap: 28px; padding-right: 44px;
  }
  .partner { display: flex; align-items: center; gap: 7px; font-weight: 700; font-size: 14px; }
  .partner-a { color: var(--partner-a); }
  .partner-b { color: var(--partner-b); }
  .partner-mark { width: 12px; height: 12px; background: currentColor; }
</style>
</head>
<body>
<main class="poster">
  <div class="scene" role="img" aria-label="Sunset sky over a mountain shore and calm reflecting water"></div>
  <div class="elder-photo" role="img" aria-label="Photo of an American Indian elder in a fur-lined winter hood"></div>

  <h1 class="title">
    <span class="line">Bright Trails,</span>
    <span class="line"><span class="underlined">Strong</span> Spirits...</span>
  </h1>

  <p class="subtitle">The River of Life Flows<br>Through the Heart,<br>Protecting the Mind and Body</p>

  <div class="stat stat-us">
    <div class="stat-icon"><div class="map-shape" role="img" aria-label="Map of the United States"></div></div>
    <div><div class="stat-figure">5.7 Million</div><div class="stat-label">Americans have<br>Alzheimer’s disease</div></div>
  </div>

  <div class="stat stat-age">
    <svg class="stat-icon" viewBox="0 0 80 74" aria-hidden="true">
      <g fill="#1c1c1c">
        <circle cx="40" cy="6" r="5" fill="#ffffff"/><rect x="35" y="12" width="10" height="14" rx="2" fill="#ffffff"/>
        <circle cx="22" cy="24" r="5"/><rect x="17" y="30" width="10" height="14" rx="2"/>
        <circle cx="58" cy="24" r="5"/><rect x="53" y="30" width="10" height="14" rx="2"/>
        <circle cx="40" cy="34" r="5"/><rect x="35" y="40" width="10" height="14" rx="2"/>
        <circle cx="8" cy="44" r="5"/><rect x="3" y="50" width="10" height="14" rx="2"/>
        <circle cx="26" cy="48" r="5"/><rect x="21" y="54" width="10" height="14" rx="2"/>
        <circle cx="54" cy="48" r="5"/><rect x="49" y="54" width="10" height="14" rx="2"/>
        <circle cx="72" cy="44" r="5"/><rect x="67" y="50" width="10" height="14" rx="2"/>
        <circle cx="40" cy="56" r="4"/><rect x="36" y="61" width="8" height="12" rx="2"/>
      </g>
    </svg>
    <div><div class="stat-figure">1 in 10</div><div class="stat-label">People age 65 and older<br>has Alzheimer’s</div></div>
  </div>

  <div class="stat stat-tribe">
    <div class="stat-icon"><div class="headdress-shape" role="img" aria-label="Profile of an elder wearing a feather headdress"></div></div>
    <div><div class="stat-figure">1 in 3</div><div class="stat-label">American Indians over<br>65 develop dementia,<br>including Alzheimer’s</div></div>
  </div>

  <p class="risk-note">Elders with <strong>diabetes, heart disease,</strong> or <strong>high blood pressure</strong> have a much higher risk of developing Alzheimer’s or other dementias</p>

  <div class="clock" role="img" aria-label="Wall clock"></div>
  <div class="appointment">
    <div class="appointment-head">MAKE AN APPOINTMENT</div>
    <div class="appointment-body">with your doctor today to<br>talk about how to keep your<br>mind and heart healthy.</div>
  </div>

  <footer class="footer">
    <div class="partner partner-a">Tribal Health Alliance</div>
    <div class="partner partner-b"><span class="partner-mark"></span>Elder Wellness Circle</div>
  </footer>
</main>
</body>
</html>
```